Income Tax Flyer - Updates Needed

Just need to update this flyer design and give it a new look. We would like to keep all the same wording but make it stand out a little more. Our selling point is the "Same Day Tax Advance up to $6,000"

Lending, Small Loans, Tax Services, Title Loans, Personal Loans

```html
<!DOCTYPE html>
<html lang="en">
<head>
<meta charset="utf-8">
<title>Same Day Tax Advance Flyer</title>
<link rel="stylesheet" href="https://fonts.googleapis.com/css2?family=Montserrat:wght@800;900&family=Poppins:wght@400;500;600;700;800&display=swap">
<style>
  :root {
    --paper: #ffffff;
    --ink: #2a2a2a;
    --green: #0f5a2e;
    --red: #d3202b;
    --red-deep: #a8141d;
    --night: #1f1f1f;
    --night-soft: #2b2b2b;
    --gold: #f7d417;
    --muted: #e6e6e6;
  }
  * { box-sizing: border-box; margin: 0; padding: 0; }
  html, body { width: 838px; height: 1200px; overflow: hidden; background: var(--paper); }
  body { font-family: "Poppins", sans-serif; color: var(--ink); }
  .flyer { position: relative; width: 838px; height: 1200px; overflow: hidden; background: var(--paper); }

  .money-scatter { position: absolute; border-radius: 6px; }
  .money-scatter.top-left { left: 0; top: 0; width: 230px; height: 170px; background: radial-gradient(ellipse at 25% 25%, #b9c2b4 0%, rgba(220,226,216,.6) 45%, rgba(255,255,255,0) 75%); }
  .money-scatter.top-right { right: 0; top: 0; width: 280px; height: 330px; background: radial-gradient(ellipse at 75% 25%, #b3bdae 0%, rgba(218,224,214,.6) 45%, rgba(255,255,255,0) 75%); }
  .money-scatter.left-edge { left: 0; top: 330px; width: 90px; height: 180px; background: radial-gradient(ellipse at 10% 50%, #c4ccbf 0%, rgba(255,255,255,0) 70%); }
  .money-scatter.right-edge { right: 0; top: 470px; width: 100px; height: 180px; background: radial-gradient(ellipse at 90% 50%, #c4ccbf 0%, rgba(255,255,255,0) 70%); }
  .money-scatter.by-amount { left: 600px; top: 700px; width: 200px; height: 70px; background: radial-gradient(ellipse at 50% 50%, #bcc5b7 0%, rgba(255,255,255,0) 70%); }

  .brand { position: absolute; top: 88px; left: 0; width: 838px; display: flex; justify-content: center; align-items: center; gap: 12px; }
  .brand-dot { width: 30px; height: 30px; border-radius: 50%; background: var(--green); }
  .brand-name { font-family: "Poppins", sans-serif; font-weight: 600; font-size: 34px; color: var(--green); letter-spacing: .2px; }

  .happy-client { position: absolute; left: 0; top: 660px; width: 220px; height: 300px; background: linear-gradient(180deg, #e9e4df 0%, #f4f4f4 40%, #d9d9dc 100%); border-radius: 0 60px 0 0; }

  .artwork { position: absolute; left: 0; top: 0; width: 838px; height: 1200px; }
  .headline { font-family: "Montserrat", sans-serif; font-weight: 900; }

  .tagline { position: absolute; top: 852px; left: 0; width: 838px; text-align: center; color: var(--paper); }
  .tagline .lead { font-size: 22px; line-height: 26px; font-weight: 400; }
  .tagline .punch { margin-top: 6px; font-family: "Poppins", sans-serif; font-weight: 800; font-size: 38px; line-height: 42px; color: var(--gold); letter-spacing: .5px; }

  .perks { position: absolute; top: 977px; left: 58px; width: 722px; display: flex; gap: 17px; list-style: none; }
  .perk { flex: 1; height: 64px; border: 1.5px dashed #8a8a8a; border-radius: 32px; display: flex; align-items: center; gap: 10px; padding-left: 10px; color: var(--paper); font-size: 18px; line-height: 20px; font-weight: 500; }
  .perk-icon { width: 40px; height: 40px; flex: none; }

  .contact { position: absolute; top: 1062px; left: 58px; color: var(--paper); }
  .contact-label { font-size: 22px; font-weight: 400; letter-spacing: .5px; }
  .contact-label strong { color: var(--gold); font-weight: 800; }
  .phone { display: flex; align-items: center; gap: 6px; margin-top: 2px; font-size: 46px; font-weight: 700; line-height: 52px; letter-spacing: .5px; }
  .phone svg { width: 34px; height: 34px; }

  .divider { position: absolute; left: 433px; top: 1065px; width: 2px; height: 105px; background: #6a6a6a; }

  .location { position: absolute; top: 1068px; left: 446px; color: var(--paper); font-size: 20px; line-height: 26px; }
  .location-name { display: flex; align-items: center; gap: 4px; font-weight: 700; font-size: 21px; }
  .location-name svg { width: 16px; height: 20px; }
  .location address { font-style: normal; padding-left: 20px; }
</style>
</head>
<body>
<main class="flyer">
  <div class="money-scatter top-left" role="img" aria-label="Falling dollar bills"></div>
  <div class="money-scatter top-right" role="img" aria-label="Falling dollar bills"></div>
  <div class="money-scatter left-edge" role="img" aria-label="Falling dollar bills"></div>
  <div class="money-scatter right-edge" role="img" aria-label="Falling dollar bills"></div>
  <div class="money-scatter by-amount" role="img" aria-label="Dollar bill resting by the amount"></div>

  <header class="brand">
    <span class="brand-dot"></span>
    <span class="brand-name">Keystone Lending Group</span>
  </header>

  <div class="happy-client" role="img" aria-label="Photo of a delighted businessman in white shirt and tie looking up at falling money"></div>

  <svg class="artwork" viewBox="0 0 838 1200" xmlns="http://www.w3.org/2000/svg">
    <g class="apply-ribbon">
      <polygon points="160,192 664,192 648,216 660,241 178,241 168,216" fill="var(--red)"/>
      <text x="419" y="228" text-anchor="middle" fill="#fff" font-family="Poppins, sans-serif" font-weight="700" font-size="27" letter-spacing="6">APPLY HERE FOR</text>
    </g>

    <text class="headline" x="166" y="327" textLength="482" lengthAdjust="spacingAndGlyphs" font-size="104" fill="var(--ink)">SAME DAY</text>

    <text class="headline" x="171" y="503" textLength="482" lengthAdjust="spacingAndGlyphs" font-size="236" fill="var(--red)">TAX</text>
    <text class="headline" x="166" y="503" textLength="482" lengthAdjust="spacingAndGlyphs" font-size="236" fill="var(--green)">TAX</text>

    <text class="headline" x="170" y="579" textLength="482" lengthAdjust="spacingAndGlyphs" font-size="98" fill="var(--red)">ADVANCE</text>
    <text class="headline" x="166" y="579" textLength="482" lengthAdjust="spacingAndGlyphs" font-size="98" fill="var(--green)">ADVANCE</text>

    <text x="419" y="612" text-anchor="middle" font-family="Poppins, sans-serif" font-weight="700" font-size="32" fill="var(--ink)">up to</text>

    <text class="headline" x="168" y="761" textLength="490" lengthAdjust="spacingAndGlyphs" font-size="150" fill="var(--green)">$6,000</text>
    <text class="headline" x="162" y="755" textLength="490" lengthAdjust="spacingAndGlyphs" font-size="150" fill="var(--red)">$6,000</text>

    <path d="M0,960 Q420,616 838,975 L838,1200 L0,1200 Z" fill="var(--red)"/>
    <path d="M0,992 Q425,652 838,1002 L838,1200 L0,1200 Z" fill="var(--night)"/>
    <path d="M0,1120 L838,1120 L838,1200 L0,1200 Z" fill="var(--night-soft)" opacity=".5"/>
  </svg>

  <section class="tagline">
    <p class="lead">File your</p>
    <p class="lead">taxes &amp; apply for an</p>
    <p class="punch">EASY ADVANCE!</p>
  </section>

  <ul class="perks">
    <li class="perk">
      <svg class="perk-icon" viewBox="0 0 40 40"><circle cx="20" cy="20" r="20" fill="var(--red)"/><circle cx="20" cy="20" r="10" fill="none" stroke="#fff" stroke-width="2.4"/><path d="M20 14v6l4 3" fill="none" stroke="#fff" stroke-width="2.4" stroke-linecap="round"/></svg>
      <span>Available in<br>24 hours or less</span>
    </li>
    <li class="perk">
      <svg class="perk-icon" viewBox="0 0 40 40"><circle cx="20" cy="20" r="20" fill="var(--red)"/><circle cx="21" cy="14" r="5" fill="#fff"/><path d="M10 25h6l5 3 8-4v3l-8 4-11-1z" fill="#fff"/></svg>
      <span>Choose your<br>Loan amount</span>
    </li>
    <li class="perk">
      <svg class="perk-icon" viewBox="0 0 40 40"><circle cx="20" cy="20" r="20" fill="var(--red)"/><circle cx="22" cy="21" r="8" fill="#fff"/><path d="M22 16v5h4" fill="none" stroke="var(--red)" stroke-width="2"/><path d="M8 17h6M7 21h6M8 25h6" stroke="#fff" stroke-width="2" stroke-linecap="round"/></svg>
      <span>Quick and<br>easy</span>
    </li>
  </ul>

  <section class="contact">
    <p class="contact-label">CONTACT US <strong>TODAY</strong></p>
    <p class="phone">
      <svg viewBox="0 0 34 34"><circle cx="17" cy="17" r="16" fill="var(--red)"/><path d="M11 9c1-1 2-1 3 0l2 3c.5 1 0 2-1 2.5 1 2.5 3 4.5 5.5 5.5.5-1 1.5-1.5 2.5-1l3 2c1 1 1 2 0 3l-1.5 1.5c-5 1-14-8-13-13z" fill="#fff"/></svg>
      345 6789 0120
    </p>
  </section>

  <div class="divider"></div>

  <section class="location">
    <p class="location-name">
      <svg viewBox="0 0 16 20"><path d="M8 0a7 7 0 0 0-7 7c0 5 7 13 7 13s7-8 7-13a7 7 0 0 0-7-7z" fill="var(--gold)"/><circle cx="8" cy="7" r="2.6" fill="var(--night)"/></svg>
      Austin – North Lamar
    </p>
    <address>2215-7 N. Lamar Blvd<br>Austin, Texas 78756</address>
  </section>
</main>
</body>
</html>
```